Ledgerline Code Works business card design.

We are a software development company that develop Software for finance companies and related industries.

We need a 2 sided business card designed. We have a new logo already designed (see attached eps and ai) We are after a clean simple corporate look. One side with just our logo, and the second side with our details.

Greg Halvorsen
Managing Director

Suite 5 Level 8, 147 Marlow Street Sydney NSW 2000

Direct: +61 2 9387 4625
Mobile: +61 4 1736 8490
Email: gregh@lcw.net.au
Web: www.lcw.net.au

I have included 2 logo files an .ai and .eps. I noticed that the lines either side of the partners looks a bit jaggered and needs to be made sharper.

I would like to introduce a little colour somewhere rather than having it all black and white. But not over the top, keeping with a simple clean corporate look. Perhaps a light blue on some of the text?

If you have other ideas would be pleased to review

Regards

Greg H.

```html
<!DOCTYPE html>
<html lang="en">
<head>
<meta charset="utf-8">
<title>Ledgerline Code Works – Business Card</title>
<link href="https://fonts.googleapis.com/css2?family=Montserrat:wght@700&family=Open+Sans:wght@400;600&display=swap" rel="stylesheet">
<style>
  :root {
    --bg: #e9e9ea;
    --card-black: #0b0b0c;
    --card-black-soft: #1c1c1e;
    --sky: #7cc0ea;
    --sky-light: #a9d8f5;
    --sky-deep: #3f93d6;
    --white: #ffffff;
    --muted: #d9d9d9;
  }
  * { box-sizing: border-box; margin: 0; padding: 0; }
  html, body { width: 1200px; height: 913px; overflow: hidden; }
  body {
    background: var(--bg);
    display: flex;
    align-items: center;
    justify-content: center;
    gap: 40px;
    font-family: "Open Sans", Arial, sans-serif;
  }
  .card {
    position: relative;
    width: 540px;
    height: 309px;
    border-radius: 4px;
    overflow: hidden;
    background: linear-gradient(160deg, var(--card-black-soft) 0%, var(--card-black) 55%);
    box-shadow: 0 6px 18px rgba(0,0,0,.25);
  }
  .brand {
    position: absolute;
    display: flex;
    align-items: center;
    gap: 12px;
  }
  .brand-mark {
    width: 26px;
    height: 26px;
    background: var(--white);
    flex: none;
  }
  .brand-name {
    font-family: "Montserrat", Arial, sans-serif;
    font-weight: 700;
    font-size: 19px;
    letter-spacing: 1.5px;
    text-transform: uppercase;
    color: var(--white);
    white-space: nowrap;
  }
  .card-front .brand { left: 50%; top: 50%; transform: translate(-50%, -50%); }

  .card-back .brand { left: 32px; top: 150px; }
  .card-back .brand-name { font-size: 16px; }
  .wave { position: absolute; inset: 0; }
  .person {
    position: absolute;
    right: 26px;
    top: 22px;
    text-align: right;
  }
  .person-name { color: var(--sky); font-weight: 600; font-size: 15px; }
  .person-title { color: var(--white); font-size: 11px; margin-top: 2px; }
  .contact {
    position: absolute;
    right: 22px;
    top: 92px;
    list-style: none;
    text-align: right;
    color: var(--white);
    font-size: 11px;
    line-height: 17px;
  }
  .contact li { display: flex; justify-content: flex-end; align-items: center; gap: 8px; }
  .contact svg { width: 10px; height: 10px; flex: none; fill: var(--white); }
  .contact .address { display: block; padding-right: 18px; }
</style>
</head>
<body>

  <section class="card card-front" aria-label="Card front">
    <div class="brand">
      <span class="brand-mark"></span>
      <span class="brand-name">Ledgerline Code Works</span>
    </div>
  </section>

  <section class="card card-back" aria-label="Card back">
    <svg class="wave" viewBox="0 0 540 309" preserveAspectRatio="none" aria-hidden="true">
      <path d="M540 70 C470 80 440 140 420 200 C395 265 300 290 0 292 L0 309 L540 309 Z" fill="var(--sky-light)"/>
      <path d="M540 70 C470 80 440 140 420 200 C395 265 300 290 0 292" fill="none" stroke="var(--card-black)" stroke-width="9"/>
      <path d="M520 76 C450 110 430 170 405 225 C380 272 280 296 0 300" fill="none" stroke="var(--card-black)" stroke-width="4"/>
      <path d="M0 305 C250 300 360 290 420 260 C450 245 500 240 540 235 L540 309 L0 309 Z" fill="var(--sky-deep)" opacity=".55"/>
    </svg>

    <div class="brand">
      <span class="brand-mark"></span>
      <span class="brand-name">Ledgerline Code Works</span>
    </div>

    <div class="person">
      <div class="person-name">Greg Halvorsen</div>
      <div class="person-title">Managing Director</div>
    </div>

    <ul class="contact">
      <li>+61 2 9387 4625
        <svg viewBox="0 0 10 10"><path d="M2 0h2l1 3-1.5 1a6 6 0 0 0 2.5 2.5L7 5l3 1v2c0 1-1 2-2 2A8 8 0 0 1 0 2c0-1 1-2 2-2z"/></svg></li>
      <li>+61 4 1736 8490
        <svg viewBox="0 0 10 10"><path d="M2.5 0h5a1 1 0 0 1 1 1v8a1 1 0 0 1-1 1h-5a1 1 0 0 1-1-1V1a1 1 0 0 1 1-1zm.5 1.5v6h4v-6z"/></svg></li>
      <li>gregh@lcw.net.au
        <svg viewBox="0 0 10 10"><path d="M0 2h10v6H0zm1 1v.3l4 2.5 4-2.5V3z"/></svg></li>
      <li>www.lcw.net.au
        <svg viewBox="0 0 10 10"><circle cx="5" cy="5" r="4.5" fill="none" stroke="#fff"/><path d="M0.5 5h9M5 .5v9" stroke="#fff" stroke-width=".8"/></svg></li>
      <li>Suite 5 Level 8, 147
        <svg viewBox="0 0 10 10"><path d="M5 0a3.5 3.5 0 0 1 3.5 3.5C8.5 6 5 10 5 10S1.5 6 1.5 3.5A3.5 3.5 0 0 1 5 0zm0 2a1.5 1.5 0 1 0 0 3 1.5 1.5 0 0 0 0-3z"/></svg></li>
      <li class="address">Marlow Street | Sydney NSW 2000</li>
    </ul>
  </section>

</body>
</html>
```